Simple landing page for Brambles cookbook

I need a one page landingpage where customers can order the cookbook.
This is a cookbook of a collection of recipes from our deli that we used to run.
I need a landing page where customers can come and order the book. I also need it coded. I already have the domain through hostwell.
I can send the file of the book through wetransfer. It's too big to upload here. Just so you get the feel that I am looking for.
I attached a simple text as an introduction to the page. But I am open to any suggestions. I want it all to be about the experience that we are sharing the recipes with everybody and that it's for sale. The book is $29.99, shipping included.
Customers have to be able to click and buy the book from it.

Coding

Coded - Design and coding required

Number of Pages Required

1 page

Font styles to use
Sans Serif

Requirements
Must have
• Same colors as the cookbook

```html
<!DOCTYPE html>
<html lang="en">
<head>
<meta charset="utf-8">
<title>Brambles Cookbook</title>
<link rel="stylesheet" href="https://fonts.googleapis.com/css2?family=Fjalla+One&family=Roboto+Condensed:wght@700&family=Quicksand:wght@500;600&display=swap">
<style>
  :root {
    --brown-dark: #3b2312;
    --brown: #4a2c14;
    --brown-warm: #5e3a17;
    --green: #7c9a3a;
    --green-light: #8fb04a;
    --peach: #f8dfd2;
    --cream: #fbf4ec;
    --white: #ffffff;
    --grey: #555555;
  }
  * { box-sizing: border-box; margin: 0; padding: 0; }
  html, body { width: 777px; height: 1200px; overflow: hidden; background: var(--white); }
  body { position: relative; font-family: "Quicksand", sans-serif; color: var(--brown); }

  .backdrop { position: absolute; left: 0; top: 0; width: 777px; height: 1200px; }

  .brand { position: absolute; left: 95px; top: 30px; display: flex; align-items: center; gap: 8px; }
  .brand-dot { width: 14px; height: 14px; border-radius: 50%; background: var(--green); }
  .brand-name { font-family: "Fjalla One", sans-serif; font-size: 24px; letter-spacing: 1px; color: var(--cream); }

  .hero-title {
    position: absolute; left: 94px; top: 104px; width: 340px;
    font-family: "Fjalla One", sans-serif; font-size: 20px; line-height: 33px;
    letter-spacing: 2.2px; color: var(--white); text-transform: uppercase;
  }
  .includes {
    position: absolute; left: 94px; top: 214px;
    font-size: 11px; font-weight: 600; letter-spacing: 1px; color: var(--white); text-transform: uppercase;
  }
  .includes strong { color: var(--green-light); font-size: 14px; font-weight: 600; }
  .categories { position: absolute; left: 94px; top: 238px; display: flex; gap: 20px; }
  .category { display: flex; align-items: center; gap: 5px; font-size: 8.5px; letter-spacing: 0.8px; color: var(--white); }

  .btn {
    position: absolute; width: 98px; height: 24px; border-radius: 12px;
    background: var(--green); color: var(--white); text-decoration: none;
    font-family: "Fjalla One", sans-serif; font-size: 10px; letter-spacing: 1.3px;
    display: flex; align-items: center; justify-content: center;
    box-shadow: 0 3px 6px rgba(0,0,0,0.18);
  }
  .btn-hero { left: 94px; top: 268px; }
  .btn-offer { left: 177px; top: 860px; }

  .media { position: absolute; }
  .book-hero { left: 482px; top: 89px; width: 172px; height: 272px; border-radius: 2px;
    background: linear-gradient(180deg, #f2f2f2 0%, #efefef 40%, #8c7458 52%, #4c4a48 72%, #efefef 100%);
    box-shadow: 8px 14px 28px rgba(0,0,0,0.22); }
  .pretzel { left: 0; top: 410px; width: 365px; height: 200px;
    background: radial-gradient(ellipse at 50% 50%, #b26a2a 0%, #c98a44 35%, #efe4d8 68%, rgba(255,255,255,0) 100%); }
  .books-offer { left: 358px; top: 628px; width: 340px; height: 345px;
    background: linear-gradient(180deg, #ebebeb 0%, #e4e4e4 38%, #8c7458 48%, #4a4847 70%, #e6e6e6 92%);
    border-radius: 2px; box-shadow: 6px 10px 24px rgba(0,0,0,0.25); }

  .intro {
    position: absolute; left: 378px; top: 453px; width: 305px;
    font-family: "Roboto Condensed", sans-serif; font-weight: 700; font-size: 15px;
    line-height: 22.6px; letter-spacing: 1px; color: var(--brown);
  }

  .price-badge { position: absolute; left: 188px; top: 664px; width: 78px; height: 78px; }
  .price { position: absolute; left: 0; top: 20px; width: 78px; text-align: center;
    font-family: "Fjalla One", sans-serif; font-size: 20px; color: var(--white); }
  .price sup { font-size: 10px; vertical-align: -2px; }
  .shipping { position: absolute; left: 16px; top: 46px; display: flex; align-items: center; gap: 3px;
    font-size: 5.5px; line-height: 6px; color: var(--white); }

  .offer-title {
    position: absolute; left: 60px; top: 748px; width: 330px; text-align: center;
    font-family: "Fjalla One", sans-serif; font-size: 30px; line-height: 32px;
    letter-spacing: 2.4px; color: var(--brown-dark);
  }
  .offer-text { position: absolute; left: 60px; top: 822px; width: 330px; text-align: center;
    font-size: 8.5px; line-height: 12.5px; letter-spacing: 0.8px; color: var(--brown-dark); }

  .quote-box {
    position: absolute; left: 94px; top: 1028px; width: 590px; height: 130px; border-radius: 8px;
    background: linear-gradient(180deg, var(--brown-dark) 0%, var(--brown-warm) 100%);
  }
  .quote-mark {
    position: absolute; left: 369px; top: 1008px; width: 39px; height: 39px; border-radius: 50%;
    background: var(--green); box-shadow: 0 0 12px rgba(210,120,120,0.35);
    display: flex; align-items: center; justify-content: center;
  }
  .quote-text {
    position: absolute; left: 140px; top: 1070px; width: 500px; text-align: center;
    font-size: 12px; line-height: 19px; letter-spacing: 1.2px; color: var(--white); font-weight: 500;
  }
  .copyright { position: absolute; left: 0; top: 1173px; width: 777px; text-align: center;
    font-size: 9.5px; color: var(--grey); }
</style>
</head>
<body>
  <svg class="backdrop" viewBox="0 0 777 1200" aria-hidden="true">
    <defs>
      <linearGradient id="heroTone" x1="0" y1="0" x2="1" y2="0.4">
        <stop offset="0" stop-color="#3a2414"/>
        <stop offset="0.55" stop-color="#4e3420"/>
        <stop offset="1" stop-color="#7a6652"/>
      </linearGradient>
    </defs>
    <path fill="var(--peach)" d="M777 555 C690 650 590 700 430 718 C300 730 150 705 0 650 V945 H175 C320 920 520 888 777 872 Z"/>
    <path fill="#ffffff" d="M0 870 C60 905 120 925 180 945 H0 Z"/>
  </svg>

  <svg class="backdrop" viewBox="0 0 777 1200" role="img" aria-label="Photo of the deli storefront with its sign above the door">
    <path fill="url(#heroTone)" d="M0 0 H777 V297 C720 280 660 270 600 276 C480 290 330 350 190 338 C110 332 50 320 0 308 Z"/>
  </svg>

  <header class="brand">
    <span class="brand-dot"></span>
    <span class="brand-name">BRAMBLES</span>
  </header>

  <h1 class="hero-title">It’s finally here! The Brambles cookbook with all your favourite recipes</h1>
  <p class="includes">Book includes <strong>28 recipes:</strong></p>
  <ul class="categories">
    <li class="category">
      <svg width="12" height="10" viewBox="0 0 12 10" fill="none" stroke="#fff" stroke-width="0.8"><path d="M1 5 L6 1 L11 5 Z M1 5 V9 H11 V5"/></svg>Sandwiches
    </li>
    <li class="category">
      <svg width="12" height="10" viewBox="0 0 12 10" fill="none" stroke="#fff" stroke-width="0.8"><path d="M1 3 H9 L8 8 H2 Z M9 4 L11 2"/></svg>Sauces
    </li>
    <li class="category">
      <svg width="12" height="10" viewBox="0 0 12 10" fill="none" stroke="#fff" stroke-width="0.8"><path d="M1 5 C1 1 11 1 11 5 Z M1 6.5 H11 M1.5 8 H10.5 V9 H1.5 Z"/></svg>Burgers
    </li>
  </ul>
  <a class="btn btn-hero" href="#order">ORDER NOW</a>

  <div class="media book-hero" role="img" aria-label="Hardcover Brambles cookbook with a photo of the deli counter on the cover"></div>

  <div class="media pretzel" role="img" aria-label="Photo of a salted pretzel sandwich with cheese on a white plate"></div>
  <p class="intro">We can’t open another Brambles restaurant but we can offer you this compilation of our best recipies for you to make and enjoy at home. Storefront picture beside it or something like that.</p>

  <div class="price-badge" id="order">
    <svg width="78" height="78" viewBox="0 0 78 78" aria-hidden="true">
      <polygon fill="var(--green)" points="39,2 47,9 57,6 61,16 71,19 69,29 76,37 69,46 72,56 62,59 59,69 49,67 41,75 33,68 23,71 19,61 9,58 11,48 3,40 10,32 7,22 17,18 20,8 30,10"/>
    </svg>
    <div class="price"><sup>$</sup>29.99</div>
    <div class="shipping">
      <svg width="14" height="9" viewBox="0 0 14 9" fill="none" stroke="#fff" stroke-width="0.8"><path d="M1 1 H8 V7 H1 Z M8 3 H11 L13 5 V7 H8"/><circle cx="3.5" cy="7.5" r="1"/><circle cx="10.5" cy="7.5" r="1"/></svg>
      <span>Free<br>Shipping</span>
    </div>
  </div>

  <h2 class="offer-title">FAVORITE RECIPES<br>IN ONE BOOK</h2>
  <p class="offer-text">We Truly Hope You Will Enjoy Making These<br>Sandwiches Just As Much As We Did.</p>
  <a class="btn btn-offer" href="#order">ORDER NOW</a>

  <div class="media books-offer" role="img" aria-label="Two copies of the Brambles cookbook lying on top of each other"></div>

  <section class="quote-box"></section>
  <div class="quote-mark">
    <svg width="20" height="14" viewBox="0 0 20 14" fill="none" stroke="#fff" stroke-width="2"><circle cx="5" cy="5" r="3.5"/><path d="M8.5 5 C8.5 9 6 12 3 13"/><circle cx="14" cy="5" r="3.5"/><path d="M17.5 5 C17.5 9 15 12 12 13"/></svg>
  </div>
  <p class="quote-text">We can’t open another Brambles, but we can offer you this collection of our recipes for you to try out at home with your family and friends.</p>

  <footer class="copyright">Copyright 2022. Marlo Everett | All Rights Reserved</footer>
</body>
</html>
```